Brenvik Systems PowerPoint Template

Project Title: Professional & Functional PowerPoint Template (.potx) – Brenvik Systems Rebrand

Project Overview:
Brenvik Systems has recently undergone a complete rebranding, including a new logo, website, and visual identity. We need a professional, high-end PowerPoint Template (.potx) that reflects our new look while being highly functional for everyday use.

We previously had a design created, but it was built incorrectly (static images, oversized file, no Master Slides). The goal of this project is to take our new aesthetic and build a "workable" template where layouts are controlled by Master Slides and text is easily editable.

Style & Brand Direction:
The template must be an extension of our new website: https://www.brenvik-systems.example/

Aesthetic: Modern, clean, high-tech, and "Industrial Tech."

Color Palette: Please pull the primary blues, greys, and accent colors directly from the website.

Imagery/Graphics: Use clean lines and subtle tech-inspired gradients. Avoid "clutter."

Tone: Innovative, precise, and professional.

Technical Requirements (Crucial)
Format: Must be delivered as a PowerPoint Template file (** .potx **).

Functionality: All layouts must be built using Slide Masters. Users should be able to click "New Slide" and choose from specific layouts.

Native Elements: Do NOT use full-page background images for text areas. Bullet points must use native PowerPoint list functionality (not individual text boxes).

File Size: The template must be optimized and lightweight.

Fonts: Use standard professional fonts or provide the specific web-safe equivalent used on our site (e.g., Montserrat, Open Sans, etc.).

Required Slide Layouts
Please include a minimum of 10–12 Master layouts, including:
*Title Slide (2-3 variations: Dark and Light)
*Agenda/Table of Contents
*Section Header/Divider Slides
*Standard Text/Bullet Slide
*Two-Column Text Slide
*Image + Text Layouts (Left/Right variations)
*Data/Chart Slide (Styled bar/pie charts that match the brand)
*Process/Timeline Slide (Infographic style)
*Section slide

Attachments Provided
Brand Assets (.zip): Contains our new logo in various formats.

Inspiration/Existing PPT: We have attached the previous design created by our web agency. Note: Use this for visual inspiration ONLY. Do not copy the file structure, as it is technically flawed.

Deliverables
Final .potx file.

All used icons or custom graphics in vector format (if applicable).

Instruction note on any specific fonts used.

Target Market(s)

Internal communication and external (investors, customers)

Industry/Entity Type

Semiconductor, Automotive

Requirements
Must have
• A potx file

```html
<!DOCTYPE html>
<html lang="en">
<head>
<meta charset="utf-8">
<title>Brenvik Systems – Presentation Template Overview</title>
<link rel="stylesheet" href="https://fonts.googleapis.com/css2?family=Montserrat:wght@400;500;600;700;800&family=Inter:wght@800&display=swap">
<style>
  :root{
    --board:#a9a9ab;
    --navy:#0c1260;
    --navy-deep:#0a0f4e;
    --blue:#1d3cf2;
    --blue-bright:#2a55ff;
    --sky:#2f7bf0;
    --ink:#14163a;
    --paper:#f4f4f6;
    --paper-2:#e9eaee;
    --white:#ffffff;
  }
  *{box-sizing:border-box;margin:0;padding:0}
  html,body{width:1012px;height:1200px;overflow:hidden}
  body{background:var(--board);font-family:"Montserrat",sans-serif;color:var(--ink);position:relative}

  .slide{position:absolute;width:460px;height:258px;overflow:hidden;
    background:linear-gradient(125deg,var(--paper) 0%,#fbfbfc 40%,var(--paper-2) 62%,#f7f7f9 100%);
    box-shadow:0 2px 6px rgba(0,0,0,.18)}
  .col-a{left:32px}.col-b{left:521px}
  .row-1{top:38px}.row-2{top:327px}.row-3{top:616px}.row-4{top:905px}

  .header{position:absolute;left:0;top:0;width:100%;height:34px;
    background:linear-gradient(90deg,var(--navy) 0%,#121f96 55%,#1c3cd6 100%)}
  .header-title{position:absolute;left:26px;top:6px;font-size:17px;font-weight:700;color:var(--white);letter-spacing:.2px}

  .brand{position:absolute;display:flex;align-items:center;gap:4px;font-weight:700;color:var(--white);line-height:1}
  .brand-mark{display:block;background:var(--blue-bright)}
  .brand.small{right:24px;top:9px;font-size:16px}
  .brand.small .brand-mark{width:12px;height:12px}
  .brand.dark{color:var(--navy)}

  .footer{position:absolute;left:0;top:232px;width:333px;height:18px;border-radius:0 9px 9px 0;
    background:linear-gradient(90deg,var(--navy) 0%,#1734c8 100%);
    color:var(--white);font-size:6px;line-height:18px;padding-left:29px}
  .page-no{position:absolute;right:0;bottom:0;width:40px;height:36px}

  .photo{position:absolute}

  /* cover */
  .cover{background:linear-gradient(120deg,#0e1560 0%,#121a72 55%,#0b1050 100%)}
  .cover .brand{left:36px;top:62px;font-size:31px}
  .cover .brand-mark{width:24px;height:24px}
  .cover-title{position:absolute;left:35px;top:108px;font-size:17px;font-weight:700;color:var(--white);line-height:20px}
  .cover-lede{position:absolute;left:35px;top:154px;width:185px;font-size:5.9px;line-height:8.4px;color:#dfe3ff}
  .date-tag{position:absolute;left:36px;top:188px;width:57px;height:15px;background:var(--blue-bright);
    clip-path:polygon(0 0,100% 0,88% 100%,0 100%);color:var(--white);font-size:5.8px;font-weight:700;line-height:15px;padding-left:8px}
  .cover-rings{position:absolute;left:0;top:0}

  /* who we are */
  .tagline{position:absolute;left:0;width:100%;text-align:center;color:var(--sky);font-weight:600}
  .badge{position:absolute;top:101px;width:88px;height:88px}
  .badge-label{position:absolute;top:150px;width:88px;text-align:center;font-size:6px;font-weight:700;color:var(--ink)}

  /* agenda */
  .agenda-photo{left:0;top:0;width:151px;height:258px;background:linear-gradient(160deg,#3a4fa8 0%,#24348a 50%,#1b2a78 100%)}
  .agenda-rule{position:absolute;left:151px;top:0;width:2px;height:258px;background:var(--blue-bright)}
  .agenda-title{position:absolute;left:167px;top:14px;font-size:17px;font-weight:700;color:var(--ink)}
  .agenda .brand{right:14px;top:15px;font-size:18px}
  .agenda .brand-mark{width:13px;height:13px}
  .agenda-item{position:absolute;display:flex;align-items:center;gap:5px;font-size:9.6px;font-weight:700;color:var(--ink);white-space:nowrap}
  .agenda-item svg{flex:none}

  /* about */
  .about-kicker{position:absolute;left:26px;top:48px;font-size:7.4px;font-weight:700}
  .about-copy{position:absolute;left:26px;width:410px;font-size:6.2px;line-height:8.6px;color:#2a2c44}
  .stat{position:absolute;top:166px}
  .stat-num{font-size:18px;font-weight:700;color:var(--blue);line-height:20px}
  .stat-label{font-size:4.8px;font-weight:700;margin-top:2px}

  /* vision */
  .vision-photo{left:26px;top:73px;width:183px;height:143px;background:radial-gradient(ellipse at 50% 45%,#8fd0ee 0%,#4b8fc4 45%,#1d3560 100%)}
  .vision-copy{position:absolute;left:223px;top:83px;width:200px;font-size:5.9px;line-height:8.4px;color:#2a2c44}
  .pillar{position:absolute;top:125px;width:60px}
  .pillar-title{margin-top:3px;font-size:6.2px;font-weight:700;line-height:8px}
  .pillar-text{margin-top:3px;font-size:4.1px;line-height:5.6px;color:#3a3c55}

  /* services */
  .lens{left:163px;top:57px;width:135px;height:159px;border-radius:8px 8px 50% 50%/8px 8px 18% 18%;
    background:linear-gradient(180deg,#2a2c33 0%,#6b6e78 40%,#1a1b20 70%,#c7d6ea 85%,#e8eef7 100%)}
  .service-name{position:absolute;font-size:10px;font-weight:600;line-height:12px}
  .service-text{position:absolute;font-size:6.1px;font-weight:700;line-height:7.3px}
  .callouts{position:absolute;left:0;top:0}

  /* closing */
  .closing{background:linear-gradient(180deg,#0d135a 0%,#1a2a9c 60%,#2437bd 100%)}
  .closing .brand{left:0;width:100%;justify-content:center;top:83px;font-size:28px;gap:7px}
  .closing .brand-mark{width:22px;height:22px}
  .thanks{position:absolute;left:0;width:100%;top:116px;text-align:center;font-family:"Inter",sans-serif;font-weight:800;font-size:47px;color:var(--white);letter-spacing:-.5px}
</style>
</head>
<body>

<!-- 01 cover -->
<section class="slide cover col-a row-1" role="img" aria-label="Dark navy title slide with a faint silhouette of transmission towers">
  <svg class="cover-rings" width="460" height="258" viewBox="0 0 460 258">
    <circle cx="379" cy="129" r="126" fill="none" stroke="#fff" stroke-width="5"/>
    <circle cx="379" cy="129" r="106" fill="none" stroke="#fff" stroke-width="5"/>
    <circle cx="379" cy="129" r="84" fill="#2a3c8c"/>
  </svg>
  <div class="photo" role="img" aria-label="Photo of a laser cutting head etching a metal sheet with sparks"
       style="left:295px;top:45px;width:168px;height:168px;border-radius:50%;background:radial-gradient(circle at 55% 70%,#f3b25a 0%,#7b6a72 18%,#41507e 45%,#24336a 100%)"></div>
  <svg style="position:absolute;left:253px;top:28px" width="60" height="60" viewBox="0 0 60 60">
    <circle cx="30" cy="30" r="30" fill="#2a55ff"/>
    <g stroke="#fff" stroke-width="2.4" stroke-linecap="round">
      <line x1="16" y1="30" x2="44" y2="30"/>
    </g>
  </svg>
  <div class="brand"><span class="brand-mark"></span>BRENVIK</div>
  <h1 class="cover-title">Enlightened<br>Engineering</h1>
  <p class="cover-lede">For industries driving tech forward, Brenvik is the most advanced laser-based manufacturing partner, unlocking the power of light for cleaner, smarter, more scalable production.</p>
  <div class="date-tag">Feb 25, 2026</div>
</section>

<!-- 05 who we are -->
<section class="slide col-b row-1">
  <header class="header"><h2 class="header-title">Who We Are</h2><div class="brand small"><span class="brand-mark"></span>BRENVIK</div></header>
  <p class="tagline" style="top:61px;font-size:11px">Partner with precision</p>
  <svg width="0" height="0" style="position:absolute">
    <defs>
      <filter id="soft" x="-20%" y="-20%" width="140%" height="150%"><feDropShadow dx="0" dy="2" stdDeviation="2.5" flood-color="#000" flood-opacity=".18"/></filter>
      <clipPath id="cap"><rect x="0" y="0" width="88" height="44"/></clipPath>
    </defs>
  </svg>
  <svg class="badge" style="left:33px" viewBox="0 0 88 88"><circle cx="44" cy="44" r="41" fill="#fff" filter="url(#soft)"/><circle cx="44" cy="44" r="41" fill="none" stroke="#0c1260" stroke-width="2.5" clip-path="url(#cap)"/><circle cx="44" cy="44" r="34" fill="#1d3cf2" clip-path="url(#cap)"/><g fill="#fff"><circle cx="38" cy="30" r="6"/><rect x="46" y="25" width="9" height="2"/><rect x="46" y="29" width="9" height="2"/><rect x="46" y="33" width="9" height="2"/></g></svg>
  <span class="badge-label" style="left:33px">Minimize cost</span>
  <svg class="badge" style="left:137px" viewBox="0 0 88 88"><circle cx="44" cy="44" r="41" fill="#fff" filter="url(#soft)"/><circle cx="44" cy="44" r="41" fill="none" stroke="#0c1260" stroke-width="2.5" clip-path="url(#cap)"/><circle cx="44" cy="44" r="34" fill="#1d3cf2" clip-path="url(#cap)"/><g fill="none" stroke="#fff" stroke-width="2"><circle cx="44" cy="30" r="8"/><circle cx="44" cy="30" r="4"/><line x1="44" y1="30" x2="53" y2="21"/></g></svg>
  <span class="badge-label" style="left:137px">Reduce waste</span>
  <svg class="badge" style="left:242px" viewBox="0 0 88 88"><circle cx="44" cy="44" r="41" fill="#fff" filter="url(#soft)"/><circle cx="44" cy="44" r="41" fill="none" stroke="#0c1260" stroke-width="2.5" clip-path="url(#cap)"/><circle cx="44" cy="44" r="34" fill="#1d3cf2" clip-path="url(#cap)"/><g fill="none" stroke="#fff" stroke-width="2"><circle cx="38" cy="24" r="3"/><circle cx="50" cy="24" r="3"/><path d="M38 27v10M50 27v10M36 37h16"/></g></svg>
  <span class="badge-label" style="left:242px">Improve quality</span>
  <svg class="badge" style="left:346px" viewBox="0 0 88 88"><circle cx="44" cy="44" r="41" fill="#fff" filter="url(#soft)"/><circle cx="44" cy="44" r="41" fill="none" stroke="#0c1260" stroke-width="2.5" clip-path="url(#cap)"/><circle cx="44" cy="44" r="34" fill="#1d3cf2" clip-path="url(#cap)"/><g fill="none" stroke="#fff" stroke-width="2"><circle cx="44" cy="27" r="7"/><path d="M40 33l-3 7 4-1 3 3M48 33l3 7-4-1-3 3"/></g></svg>
  <span class="badge-label" style="left:346px">Increase yields</span>
  <div class="footer">© Copyrights 2026 | All Rights Reserved</div>
  <svg class="page-no" viewBox="0 0 40 36"><circle cx="23" cy="33" r="19" fill="none" stroke="#0c1260" stroke-width="2.4"/><circle cx="23" cy="33" r="15" fill="none" stroke="#1d3cf2" stroke-width="1.2"/><text x="23" y="32" text-anchor="middle" font-family="Montserrat,sans-serif" font-size="6.5" font-weight="700" fill="#2a55ff">05</text></svg>
</section>

<!-- 02 agenda -->
<section class="slide agenda col-a row-2">
  <div class="photo agenda-photo" role="img" aria-label="Photo of two colleagues reviewing a tablet in an office, blue duotone"></div>
  <div class="agenda-rule"></div>
  <h2 class="agenda-title">Agenda</h2>
  <div class="brand dark"><span class="brand-mark"></span>BRENVIK</div>
  <div class="agenda-item" style="left:167px;top:76px"><svg width="25" height="25" viewBox="0 0 25 25"><path d="M21 5A11 11 0 1 0 21 20" fill="none" stroke="#0c1260" stroke-width="1.6"/><path d="M19 7.5A8 8 0 1 0 19 17.5" fill="none" stroke="#0c1260" stroke-width=".9"/><text x="13" y="15" text-anchor="middle" font-size="5.5" font-weight="700" fill="#2a55ff" font-family="Montserrat,sans-serif">01</text></svg>Who We Are</div>
  <div class="agenda-item" style="left:167px;top:123px"><svg width="25" height="25" viewBox="0 0 25 25"><path d="M21 5A11 11 0 1 0 21 20" fill="none" stroke="#0c1260" stroke-width="1.6"/><path d="M19 7.5A8 8 0 1 0 19 17.5" fill="none" stroke="#0c1260" stroke-width=".9"/><text x="13" y="15" text-anchor="middle" font-size="5.5" font-weight="700" fill="#2a55ff" font-family="Montserrat,sans-serif">02</text></svg>Our Services</div>
  <div class="agenda-item" style="left:167px;top:178px"><svg width="25" height="25" viewBox="0 0 25 25"><path d="M21 5A11 11 0 1 0 21 20" fill="none" stroke="#0c1260" stroke-width="1.6"/><path d="M19 7.5A8 8 0 1 0 19 17.5" fill="none" stroke="#0c1260" stroke-width=".9"/><text x="13" y="15" text-anchor="middle" font-size="5.5" font-weight="700" fill="#2a55ff" font-family="Montserrat,sans-serif">03</text></svg>Shiftwell Resources</div>
  <div class="agenda-item" style="left:294px;top:76px"><svg width="25" height="25" viewBox="0 0 25 25"><path d="M21 5A11 11 0 1 0 21 20" fill="none" stroke="#0c1260" stroke-width="1.6"/><path d="M19 7.5A8 8 0 1 0 19 17.5" fill="none" stroke="#0c1260" stroke-width=".9"/><text x="13" y="15" text-anchor="middle" font-size="5.5" font-weight="700" fill="#2a55ff" font-family="Montserrat,sans-serif">04</text></svg>Latest articles</div>
  <div class="agenda-item" style="left:294px;top:123px"><svg width="25" height="25" viewBox="0 0 25 25"><path d="M21 5A11 11 0 1 0 21 20" fill="none" stroke="#0c1260" stroke-width="1.6"/><path d="M19 7.5A8 8 0 1 0 19 17.5" fill="none" stroke="#0c1260" stroke-width=".9"/><text x="13" y="15" text-anchor="middle" font-size="5.5" font-weight="700" fill="#2a55ff" font-family="Montserrat,sans-serif">05</text></svg>Our People</div>
  <div class="agenda-item" style="left:294px;top:178px"><svg width="25" height="25" viewBox="0 0 25 25"><path d="M21 5A11 11 0 1 0 21 20" fill="none" stroke="#0c1260" stroke-width="1.6"/><path d="M19 7.5A8 8 0 1 0 19 17.5" fill="none" stroke="#0c1260" stroke-width=".9"/><text x="13" y="15" text-anchor="middle" font-size="5.5" font-weight="700" fill="#2a55ff" font-family="Montserrat,sans-serif">06</text></svg>Business Development</div>
  <svg class="page-no" viewBox="0 0 40 36"><circle cx="23" cy="33" r="19" fill="none" stroke="#0c1260" stroke-width="2.4"/><circle cx="23" cy="33" r="15" fill="none" stroke="#1d3cf2" stroke-width="1.2"/><text x="23" y="32" text-anchor="middle" font-family="Montserrat,sans-serif" font-size="6.5" font-weight="700" fill="#2a55ff">02</text></svg>
</section>

<!-- 06 section divider -->
<section class="slide col-b row-2">
  <header class="header"><h2 class="header-title">Section Divider</h2><div class="brand small"><span class="brand-mark"></span>BRENVIK</div></header>
  <div class="footer">© Copyrights 2026 | All Rights Reserved</div>
  <svg class="page-no" viewBox="0 0 40 36"><circle cx="23" cy="33" r="19" fill="none" stroke="#0c1260" stroke-width="2.4"/><circle cx="23" cy="33" r="15" fill="none" stroke="#1d3cf2" stroke-width="1.2"/><text x="23" y="32" text-anchor="middle" font-family="Montserrat,sans-serif" font-size="6.5" font-weight="700" fill="#2a55ff">06</text></svg>
</section>

<!-- 03 about -->
<section class="slide col-a row-3">
  <header class="header"><h2 class="header-title">About Us</h2><div class="brand small"><span class="brand-mark"></span>BRENVIK</div></header>
  <h3 class="about-kicker">Illuminating tomorrow's manufacturing</h3>
  <p class="about-copy" style="top:64px">We're the Westbrook spinout turning light into breakthrough precision—building the backbone of an electrified future.</p>
  <p class="about-copy" style="top:78px">Founded in 2014, we emerged to replace wasteful mechanical manufacturing with laser precision. Today we deliver 2.2-2.3 wafers per mm with $132M in funding.</p>
  <p class="about-copy" style="top:104px">We don't optimize existing processes—we eliminate them. Our breakthrough approach creates manufacturing methods that seemed impossible years ago.</p>
  <p class="about-copy" style="top:130px">From California to facilities worldwide, our process reduces costs by more than 60% while cutting waste—making clean technology more accessible and efficient.</p>
  <div class="stat" style="left:26px"><div class="stat-num">2014</div><div class="stat-label">Founded in</div></div>
  <div class="stat" style="left:98px"><div class="stat-num">2–3x</div><div class="stat-label">improvement in wafer throughput</div></div>
  <div class="stat" style="left:205px"><div class="stat-num">+60%</div><div class="stat-label">cost savings at scale</div></div>
  <div class="footer">© Copyrights 2026 | All Rights Reserved</div>
  <svg class="page-no" viewBox="0 0 40 36"><circle cx="23" cy="33" r="19" fill="none" stroke="#0c1260" stroke-width="2.4"/><circle cx="23" cy="33" r="15" fill="none" stroke="#1d3cf2" stroke-width="1.2"/><text x="23" y="32" text-anchor="middle" font-family="Montserrat,sans-serif" font-size="6.5" font-weight="700" fill="#2a55ff">03</text></svg>
</section>

<!-- 07 vision -->
<section class="slide col-b row-3">
  <header class="header"><h2 class="header-title">Our Vision</h2><div class="brand small"><span class="brand-mark"></span>BRENVIK</div></header>
  <p class="tagline" style="top:47px;font-size:10.6px">Built at Westbrook, backed by visionaries</p>
  <div class="photo vision-photo" role="img" aria-label="Photo of a laser beam processing a silicon carbide wafer"></div>
  <p class="vision-copy">Founded in 2014 as a Westbrook spinout, we combine breakthrough research with real-world execution. With $132M in funding from leading VCs and government partners, we're building the</p>
  <div class="pillar" style="left:223px">
    <svg width="34" height="34" viewBox="0 0 34 34"><path d="M29 6A15 15 0 1 0 29 28" fill="none" stroke="#0c1260" stroke-width="2.4"/><path d="M26 9A11 11 0 1 0 26 25" fill="none" stroke="#0c1260" stroke-width="1.2"/><rect x="13" y="11" width="10" height="12" rx="1" fill="#2f7bf0"/><rect x="15" y="16" width="2" height="5" fill="#fff"/><rect x="19" y="14" width="2" height="7" fill="#fff"/></svg>
    <div class="pillar-title">Westbrook<br>innovation</div>
    <div class="pillar-text">Academic rigor meets manufacturing execution</div>
  </div>
  <div class="pillar" style="left:297px">
    <svg width="34" height="34" viewBox="0 0 34 34"><path d="M29 6A15 15 0 1 0 29 28" fill="none" stroke="#0c1260" stroke-width="2.4"/><path d="M26 9A11 11 0 1 0 26 25" fill="none" stroke="#0c1260" stroke-width="1.2"/><rect x="13" y="10" width="9" height="13" rx="1" fill="#2f7bf0"/><path d="M15 17l2 2 3-4" fill="none" stroke="#fff" stroke-width="1.3"/></svg>
    <div class="pillar-title">Industry<br>leadership</div>
    <div class="pillar-text">Backed by VCs and energy agencies driving deep-tech innovation</div>
  </div>
  <div class="pillar" style="left:372px">
    <svg width="34" height="34" viewBox="0 0 34 34"><path d="M29 6A15 15 0 1 0 29 28" fill="none" stroke="#0c1260" stroke-width="2.4"/><path d="M26 9A11 11 0 1 0 26 25" fill="none" stroke="#0c1260" stroke-width="1.2"/><path d="M12 15h4l7-4v12l-7-4h-4z" fill="#2f7bf0"/><rect x="14" y="19" width="2" height="4" fill="#2f7bf0"/></svg>
    <div class="pillar-title">News<br>Straight</div>
    <div class="pillar-text">Decades of experience in laser physics and advanced materials</div>
  </div>
  <div class="footer">© Copyrights 2026 | All Rights Reserved</div>
  <svg class="page-no" viewBox="0 0 40 36"><circle cx="23" cy="33" r="19" fill="none" stroke="#0c1260" stroke-width="2.4"/><circle cx="23" cy="33" r="15" fill="none" stroke="#1d3cf2" stroke-width="1.2"/><text x="23" y="32" text-anchor="middle" font-family="Montserrat,sans-serif" font-size="6.5" font-weight="700" fill="#2a55ff">07</text></svg>
</section>

<!-- 04 services -->
<section class="slide col-a row-4">
  <header class="header"><h2 class="header-title">Our Services</h2><div class="brand small"><span class="brand-mark"></span>BRENVIK</div></header>
  <div class="photo lens" role="img" aria-label="Illustration of a laser lens head above a glowing wafer disc"></div>
  <svg class="callouts" width="460" height="258" viewBox="0 0 460 258">
    <g fill="none" stroke="#2a55ff" stroke-width=".6">
      <polyline points="100,140 163,140 201,102"/>
      <polyline points="261,206 297,170 353,170"/>
    </g>
    <rect x="198" y="99" width="6" height="6" fill="#1d3cf2"/><rect x="199.8" y="100.8" width="2.4" height="2.4" fill="#fff"/>
    <rect x="258" y="203" width="6" height="6" fill="#1d3cf2"/><rect x="259.8" y="204.8" width="2.4" height="2.4" fill="#fff"/>
  </svg>
  <h3 class="service-name" style="right:315px;top:76px;text-align:right">Laser wafering<br>services</h3>
  <p class="service-text" style="right:315px;top:104px;width:100px;text-align:right">We deliver manufacturing excellence as a service—no equipment investment, just superior results.</p>
  <h3 class="service-name" style="left:305px;top:115px">SiC wafers</h3>
  <p class="service-text" style="left:305px;top:131px;width:112px">Production-grade wafers in multiplethicknesses —engineered to power tomorrow's breakthroughs.</p>
  <div class="footer">© Copyrights 2026 | All Rights Reserved</div>
  <svg class="page-no" viewBox="0 0 40 36"><circle cx="23" cy="33" r="19" fill="none" stroke="#0c1260" stroke-width="2.4"/><circle cx="23" cy="33" r="15" fill="none" stroke="#1d3cf2" stroke-width="1.2"/><text x="23" y="32" text-anchor="middle" font-family="Montserrat,sans-serif" font-size="6.5" font-weight="700" fill="#2a55ff">04</text></svg>
</section>

<!-- closing -->
<section class="slide closing col-b row-4" role="img" aria-label="Closing slide over a blue-toned silhouette of transmission towers">
  <div class="brand"><span class="brand-mark"></span>BRENVIK</div>
  <p class="thanks">Thank You</p>
</section>

</body>
</html>
```